Patent Law

Need to develop a home page for a patent lawyer.

Colors should go with logo, blues...

Company Name- Velun Tresk, PLLC

Company Overview-

I am an Intellectual Property Lawyer and focus on patents, copyrights, trademarks, & trade secrets. I work with small businesses and start ups in the chemical and biotech industries.

Why Us-

I am small firm that can provide large-firm service at a reasonable price. I also can charge flat-fees for entreprenuers in certain practice areas.

Services-
Intellectual Property
Patents
Copyrights
Trademarks
Trade secrets
Healthcare Compliance
Elder law
Wills
Trusts

Website we like-
http://www.quorvantlegal.example/ - within industry!!
http://www.daltrowemiko.example/
http://ulbrixtane.example/
http://thegravelcounsel.example/

Target Market(s)

My customers will be small business, specifically small start-up companies in the chemical and biotech arena.

Industry/Entity Type

Trade

Requirements
Must have
• Colors should go with logo, blues...

```html
<!DOCTYPE html>
<html lang="en">
<head>
<meta charset="utf-8">
<title>Velun Tresk, PLLC – Patent Law Firm</title>
<link rel="stylesheet" href="https://fonts.googleapis.com/css2?family=Figtree:ital,wght@0,300;0,400;0,600;0,700;1,400&display=swap">
<style>
:root{
  --header-bg:#eceee1;
  --page-bg:#f3f3f3;
  --blue:#0b88d6;
  --blue-dark:#0673b8;
  --ink:#222;
  --ink-soft:#444;
  --muted:#8a8a8a;
  --rule:#d4d4d4;
  --white:#fff;
}
*{margin:0;padding:0;box-sizing:border-box}
html,body{width:1200px;height:1001px;overflow:hidden}
body{position:relative;background:var(--page-bg);font-family:"Figtree",Arial,sans-serif;color:var(--ink)}
.abs{position:absolute}

/* header */
.site-header{position:absolute;left:0;top:0;width:1200px;height:99px;background:var(--header-bg)}
.brand{left:240px;top:30px;display:flex;align-items:center;gap:8px}
.brand-dot{width:14px;height:14px;border-radius:50%;background:var(--blue)}
.brand-name{font-size:15px;font-weight:600;letter-spacing:.06em;color:#2a2a3a;text-transform:uppercase}
.main-nav a{position:absolute;top:75px;font-size:11.5px;color:var(--ink-soft);text-decoration:none}
.main-nav a.active{color:var(--blue)}
.nav-underline{left:417px;top:95px;width:34px;height:4px;background:var(--blue)}
.call{right:265px;top:9px;text-align:right}
.call-q{font-size:13px;color:#555;line-height:14px}
.call-p{font-size:10px;color:#777;line-height:11px}
.call-num{font-size:18px;font-weight:700;color:#2b2b2b;line-height:22px}
.or{left:816px;top:69px;font-size:10px;color:#999}
.btn-email-sm{left:848px;top:64px;width:88px;height:24px;background:var(--blue);border-radius:2px;color:var(--white);font-size:10.5px;display:flex;align-items:center;justify-content:center;gap:6px}

/* hero */
.hero{position:absolute;left:0;top:99px;width:1200px;height:363px;
  background:radial-gradient(ellipse 380px 260px at 360px 180px,#c98a3c 0%,#8a5320 45%,transparent 75%),
  linear-gradient(90deg,#5a3414 0%,#7a4a1e 30%,#6b4420 55%,#4a3018 78%,#6a5a2a 100%)}
.hero-title{left:556px;top:190px;font-size:40px;font-weight:700;color:var(--white);line-height:46px}
.hero-sub{left:557px;top:232px;font-size:28px;font-weight:300;color:var(--white)}
.hero-copy{left:557px;top:279px;width:345px;font-size:11px;line-height:13.5px;color:var(--white)}
.btn-contact{left:557px;top:375px;width:198px;height:50px;background:var(--blue);color:var(--white)}
.btn-contact .small{position:absolute;left:16px;top:9px;font-size:11.5px}
.btn-contact .big{position:absolute;left:16px;top:21px;font-size:21px}
.btn-contact svg{position:absolute;left:154px;top:13px}

/* info columns */
.col{top:499px;width:200px}
.col h2{font-size:15px;font-weight:700;letter-spacing:.02em;color:#111;line-height:18px}
.col .tag{font-size:11px;font-style:italic;color:var(--muted);line-height:14px;margin-bottom:9px}
.col p{font-size:9px;line-height:13px;color:var(--ink-soft)}
.col p.gap{margin-top:10px}
.sep{margin:0 5px}
.divider-shadow{left:200px;top:648px;width:800px;height:14px;
  background:radial-gradient(ellipse 400px 7px at 50% 0,rgba(0,0,0,.16),transparent 100%)}

/* cta */
.cta{left:0;top:698px;width:1200px;text-align:center}
.cta h3{font-size:28px;font-weight:300;color:var(--blue);line-height:34px;margin-bottom:6px}
.cta .lead{font-size:15px;line-height:19px;color:var(--ink)}
.cta .hours{margin-top:14px;font-size:11px;color:var(--ink-soft);line-height:17px}
.cta .hours b{font-size:15px;font-weight:700;color:var(--blue)}
.btn-send{left:528px;top:851px;width:145px;height:38px;border-radius:2px;
  background:linear-gradient(#19a0ec,var(--blue-dark));color:var(--white);font-size:15px;font-weight:700;
  display:flex;align-items:center;justify-content:center}

/* footer */
.footer-rule{left:234px;top:926px;width:732px;height:1px;background:var(--rule)}
.copyright{left:290px;top:964px;font-size:9.5px;color:var(--ink-soft)}
.footer-nav{left:527px;top:964px;display:flex;font-size:9.5px;color:var(--ink-soft)}
.footer-nav a{color:var(--ink-soft);text-decoration:none;padding:0 11px;border-left:1px solid #aaa;line-height:13px}
.footer-nav a:first-child{padding-left:0;border-left:0;color:var(--blue)}
</style>
</head>
<body>

<header class="site-header">
  <div class="abs brand"><span class="brand-dot"></span><span class="brand-name">Velun Tresk, PLLC</span></div>
  <nav class="main-nav">
    <a class="active" style="left:419px" href="#">Home</a>
    <a style="left:478px" href="#">About</a>
    <a style="left:537px" href="#">Resources</a>
    <a style="left:617px" href="#">Practice Areas</a>
  </nav>
  <div class="abs nav-underline"></div>
  <div class="abs call">
    <div class="call-q">Any Questions?</div>
    <div class="call-p">Please Call</div>
    <div class="call-num">888-555-0192</div>
  </div>
  <div class="abs or">OR</div>
  <div class="abs btn-email-sm">
    <svg width="13" height="9" viewBox="0 0 13 9"><rect x=".5" y=".5" width="12" height="8" fill="#fff"/><path d="M.5 .5 6.5 5 12.5 .5" fill="none" stroke="#0b88d6"/></svg>
    Send Email
  </div>
</header>

<section class="hero" role="img" aria-label="Blurred photo of brass scales of justice on a courtroom desk"></section>
<h1 class="abs hero-title">Velun Tresk</h1>
<div class="abs hero-sub">Paten Law Firm</div>
<p class="abs hero-copy">I am an Intellectual Property Lawyer and focus on patents, copyrights, trademarks, &amp; trade secrets. I work with small businesses and start ups in the chemical and biotech industries.</p>
<div class="abs btn-contact">
  <span class="small">Need Help?</span>
  <span class="big">Contact Me</span>
  <svg width="25" height="25" viewBox="0 0 25 25"><circle cx="12.5" cy="12.5" r="11" fill="none" stroke="#fff" stroke-width="1.6"/><path d="M10.5 8 15 12.5 10.5 17" fill="none" stroke="#fff" stroke-width="1.6"/></svg>
</div>

<div class="abs col" style="left:277px">
  <h2>WHY US?</h2>
  <div class="tag">This is a reason why you choose us</div>
  <p>I am small firm that can provide large-firm service at a reasonable price. I also can charge flat-fees for entreprenuers in certain practice areas.</p>
</div>
<div class="abs col" style="left:520px;width:210px">
  <h2>WHAT WE DO</h2>
  <div class="tag">What can we do for you?</div>
  <p>Intellectual Property<span class="sep">I</span>Patents<span class="sep">I</span>Copyrights<br>Trademarks<span class="sep">I</span>Trade secrets<span class="sep">I</span>Healthcare<br>Compliance<span class="sep">I</span>Elder law<span class="sep">I</span>Wills<span class="sep">I</span>Trusts</p>
</div>
<div class="abs col" style="left:763px">
  <h2>CONTACT INFO</h2>
  <div class="tag">Where you can find us?</div>
  <p>212th ST. Marlow - Oak Park<br>KANSAS - MISSOURI 55190</p>
  <p class="gap">Phone. 888-555-0192<br>Email. client@veluntresk.example</p>
</div>

<div class="abs divider-shadow"></div>

<section class="abs cta">
  <h3>Velun Tresk - Patent Lawyer.</h3>
  <p class="lead">For business consultation and information of your patents, please contact us.<br>We are ready to serve you.</p>
  <p class="hours">Open <b>08am - 16pm</b><br>Appointment <b>888-555-0192</b></p>
</section>
<div class="abs btn-send">SEND US EMAIL</div>

<div class="abs footer-rule"></div>
<div class="abs copyright">Velun Tresk | © 2014 All Right Reserved</div>
<nav class="abs footer-nav">
  <a href="#">Home</a><a href="#">Pricing</a><a href="#">Resource</a><a href="#">Terms &amp; Condition</a><a href="#">Privacy Policy</a><a href="#">Fees</a>
</nav>

</body>
</html>
```